Healthcare and Professional IT Services Company need a redesigned business card

We are a IT Services company that targets small medical practices and professional business such as Attorneys, Accounts, Architects etc. We want to communicate a professional yet friendly image using recent logo redesign here on ArtHarbor. Like to see the colors blue and orange in the design. Must use the Tall Pine Computing as displayed in the new logo - then also want to incorporate the fish logo as well.

Target Market(s)

Small medical and professional services

Industry/Entity Type

It Company

Contact Information for Business Card

The usual stuff, place for name address phone website. Also maybe our tagline which is "Rooted in technology"

Requirements
Must have
• My new logo and the fish somewhere on the card

```html
<!DOCTYPE html>
<html lang="en">
<head>
<meta charset="utf-8">
<title>Tall Pine Computing – Business Card</title>
<link rel="stylesheet" href="https://fonts.googleapis.com/css2?family=PT+Sans:wght@400;700&display=swap">
<style>
  :root {
    --stage: #3b3b3b;
    --card-white: #f7f7f7;
    --brand-blue: #0a8fd6;
    --brand-blue-deep: #1565b0;
    --brand-orange: #f28c1b;
    --ink: #3a3a3a;
    --white: #ffffff;
  }
  * { margin: 0; padding: 0; box-sizing: border-box; }
  html, body {
    width: 1200px; height: 750px; overflow: hidden;
    background: var(--stage);
    font-family: "PT Sans", sans-serif;
  }
  .sheet { position: relative; width: 1200px; height: 750px; }
  .card {
    position: absolute; top: 228px; width: 461px; height: 262px; overflow: hidden;
  }
  .card-front { left: 124px; background: var(--card-white); }
  .card-back { left: 618px; background: var(--brand-blue); }
  .corner-art { position: absolute; inset: 0; width: 100%; height: 100%; }

  .brand-lockup {
    position: absolute; right: 22px; top: 70px;
    display: flex; align-items: center; gap: 10px;
  }
  .brand-dot {
    width: 22px; height: 22px; border-radius: 50%;
    background: var(--brand-blue);
  }
  .brand-name {
    color: var(--brand-blue); font-weight: 700; font-size: 24px;
    line-height: 1.05; text-align: right;
  }

  .contact { position: absolute; left: 23px; top: 119px; color: var(--ink); }
  .contact-name { color: var(--brand-blue); font-size: 19px; font-weight: 700; line-height: 22px; }
  .contact-title { color: var(--brand-orange); font-size: 13px; line-height: 16px; margin-bottom: 7px; }
  .contact-address { font-size: 11px; line-height: 14px; margin-bottom: 3px; }
  .contact-list { list-style: none; font-size: 11px; }
  .contact-list li { display: flex; align-items: center; gap: 7px; height: 18px; }
  .contact-list svg { width: 12px; height: 12px; flex: none; }

  .back-name {
    position: absolute; left: 0; right: 0; top: 88px;
    text-align: center; color: var(--white);
    font-weight: 700; font-size: 36px; line-height: 1.1;
  }
  .back-tagline {
    position: absolute; left: 0; right: 0; top: 230px;
    text-align: center; color: var(--white); font-size: 13px; line-height: 16px;
  }
</style>
</head>
<body>
<main class="sheet">
  <section class="card card-front">
    <svg class="corner-art" viewBox="0 0 461 262" aria-hidden="true">
      <path d="M0 0 H104 Q24 34 0 106 Z" fill="var(--brand-blue)"/>
      <path d="M2 106 Q30 28 104 2" fill="none" stroke="var(--brand-blue-deep)" stroke-width="3"/>
      <path d="M461 262 H356 Q438 228 461 156 Z" fill="var(--brand-blue)"/>
      <path d="M358 260 Q432 226 459 158" fill="none" stroke="var(--brand-blue-deep)" stroke-width="3"/>
    </svg>

    <div class="brand-lockup">
      <span class="brand-dot"></span>
      <span class="brand-name">Tall Pine<br>Computing</span>
    </div>

    <div class="contact">
      <p class="contact-name">Jordan Reyes</p>
      <p class="contact-title">CEO/Founder</p>
      <p class="contact-address">214 Cedar Hollow Road<br>Juneau, Alaska 99801</p>
      <ul class="contact-list">
        <li>
          <svg viewBox="0 0 16 16"><path d="M4 1 L6.5 4.5 L5 6.5 Q6.5 9.5 9.5 11 L11.5 9.5 L15 12 L13 15 Q5 14 1 3 Z" fill="var(--brand-blue)"/></svg>
          907 555 0142
        </li>
        <li>
          <svg viewBox="0 0 16 16"><rect x="1" y="3" width="14" height="10" fill="var(--brand-blue)"/><path d="M1 3 L8 9 L15 3" fill="none" stroke="var(--white)" stroke-width="1.4"/></svg>
          hello@tallpinecomputing.com
        </li>
        <li>
          <svg viewBox="0 0 16 16"><circle cx="8" cy="8" r="7" fill="var(--brand-blue)"/><ellipse cx="8" cy="8" rx="3" ry="7" fill="none" stroke="var(--white)" stroke-width="1"/><path d="M1 8 H15" stroke="var(--white)" stroke-width="1"/></svg>
          www.tallpinecomputing.com
        </li>
      </ul>
    </div>
  </section>

  <section class="card card-back">
    <p class="back-name">Tall Pine<br>Computing</p>
    <p class="back-tagline">Rooted in technology</p>
  </section>
</main>
</body>
</html>
```